Waste management company seeks a new website design

We need a website design for an environmental services company called 'Laanemetsa Haldusgrupp.' We manage waste collection and recycling for 100K+ households and businesses across Estonia. Please use logos and colors from attached CVI file. The design should be extensively usable for our self-service portal and have a mobile-first approach as it will be turned into an app in the future. The new website should highlight our commitment to sustainability and provide easy access to our services with a clean, modern design. UX inspiration from https://ruvako.eu/et-ee/

```html
<!DOCTYPE html>
<html lang="en">
<head>
<meta charset="utf-8">
<title>Laanemetsa Haldusgrupp — Website Design</title>
<link href="https://fonts.googleapis.com/css2?family=Inter:wght@400;500;600;700&family=Lato:wght@400;700&display=swap" rel="stylesheet">
<style>
:root{
  --lime:#d5de2c;
  --lime-soft:#fafde8;
  --taupe:#978a83;
  --ink:#1d1d1b;
  --text:#3a3a38;
  --muted:#8a8a86;
  --board:#dcdcdc;
  --footer:#efefef;
  --white:#ffffff;
}
*{box-sizing:border-box;margin:0;padding:0}
html,body{width:826px;height:1200px;overflow:hidden;background:var(--board)}
body{font-family:"Lato",sans-serif;color:var(--text)}
.board{position:absolute;left:0;top:0;width:1596px;height:2320px;transform:scale(0.51754);transform-origin:0 0;background:var(--board)}
.page{position:absolute;top:59px;width:724px;height:2206px;background:var(--white);overflow:hidden;box-shadow:0 2px 8px rgba(0,0,0,.08)}
.page--a{left:51px}
.page--b{left:820px}
.abs{position:absolute}
h2,h3,h4,.brand-name,.pill{font-family:"Inter",sans-serif}

/* header */
.hero{position:absolute;left:0;top:0;width:724px;height:377px;overflow:hidden}
.hero--family{background:linear-gradient(180deg,#8e857e 0%,#948b83 55%,#8a8078 100%)}
.hero--globe{background:radial-gradient(circle at 40% 30%,#8ea24a 0%,#3c6a2a 35%,#1c3b1c 75%,#122813 100%)}
.brand{position:absolute;left:66px;top:16px;display:flex;align-items:center;gap:8px}
.brand-dot{width:38px;height:38px;border-radius:50%;background:var(--white)}
.brand-name{font-weight:600;font-size:14px;line-height:15px;color:var(--white)}
.lang{position:absolute;left:485px;top:26px;font-family:"Inter",sans-serif;font-size:10px;color:var(--white);display:flex;align-items:center;gap:4px}
.pill{display:inline-flex;align-items:center;justify-content:center;border-radius:14px;font-weight:600;font-size:9.5px;color:var(--ink);box-shadow:0 2px 3px rgba(0,0,0,.15)}
.pill--lime{background:var(--lime)}
.pill--white{background:var(--white)}
.header-cta{position:absolute;left:547px;top:19px;width:74px;height:26px}
.menu{position:absolute;left:638px;top:24px}
.hero-copy{position:absolute;left:66px;width:290px;color:var(--white)}
.hero--family .hero-copy{top:106px}
.hero--globe .hero-copy{top:126px}
.hero-copy .eyebrow{font-family:"Inter",sans-serif;font-size:12px;font-weight:500}
.hero-copy h1{font-family:"Inter",sans-serif;font-weight:600;font-size:24px;margin:6px 0 8px;text-shadow:0 1px 3px rgba(0,0,0,.25)}
.hero-copy p{font-size:8.3px;line-height:16.6px}
.hero-copy .pill{width:94px;height:28px;margin-top:8px}
.hero-photo{position:absolute;left:368px;top:84px;width:430px;height:430px;border-radius:50%;background:linear-gradient(160deg,#e8b461 0%,#c98a3b 45%,#7a5a2a 100%);box-shadow:-10px -6px 0 var(--lime)}
.hero-globe{position:absolute;left:330px;top:70px;width:390px;height:300px;border-radius:50%;background:radial-gradient(circle at 55% 60%,rgba(120,220,190,.55) 0%,rgba(40,120,90,.35) 45%,rgba(0,0,0,0) 70%)}

/* section titles */
.section-title{position:absolute;left:0;width:724px;display:flex;justify-content:center;align-items:center;gap:7px;font-weight:500;font-size:20.5px;color:var(--ink)}
.section-title::before{content:"";width:20px;height:20px;border-radius:50%;background:var(--taupe)}

/* about */
.about-art{left:66px;top:462px;width:280px;height:232px;border-radius:50%;background:linear-gradient(135deg,#a89b94 0%,#978a83 50%,#d5de2c 51%,#cfd82a 100%)}
.about-text{left:373px;top:456px;width:292px;font-size:8px;line-height:16.6px}
.about-text p+p{margin-top:16.6px}
.read-more{width:93px;height:28px}

/* benefits */
.benefits{left:0;top:750px;width:724px;height:308px;background:var(--lime-soft)}
.lead{position:absolute;left:100px;width:524px;text-align:center;font-size:8.5px;line-height:16.6px;color:var(--ink)}
.card{position:absolute;top:130px;width:166px;height:125px;background:var(--lime);border-radius:10px;padding:14px 12px 0 12px}
.card h4{font-weight:500;font-size:11px;line-height:18.5px;color:var(--ink);width:118px}
.card p{font-size:7.8px;line-height:15.5px;color:#4a4a2a;margin-top:2px}
.card-icon{position:absolute;right:-18px;top:-18px;width:38px;height:38px;border-radius:50%;background:var(--lime);border:3px solid var(--white)}

/* steps */
.steps{left:66px;top:1136px;width:310px}
.steps h3{font-weight:500;font-size:15px;color:var(--ink);margin-bottom:10px}
.step{position:relative;padding-left:23px;margin-bottom:12px}
.step-num{position:absolute;left:2px;top:2px;width:10px;height:10px;border-radius:50%;background:var(--lime);font-size:6px;font-weight:700;text-align:center;line-height:10px;color:var(--ink)}
.step h5{font-family:"Inter",sans-serif;font-weight:400;font-size:10px;color:var(--ink);margin-bottom:4px}
.step p{font-size:7.8px;line-height:15.6px;color:#555}
.forest{left:409px;top:1142px;width:247px;height:264px;border-radius:8px;background:radial-gradient(circle at 50% 50%,#4f8a5c 0%,#2f6b34 45%,#1f4d24 100%)}

/* contact block */
.touch{left:67px;top:1451px;width:589px;height:245px;background:var(--lime);border-radius:14px;text-align:center;color:#2c2c10}
.touch .section-title{position:static;width:auto;margin-top:28px}
.touch .section-title::before{background:var(--ink)}
.touch p{font-size:8.6px;line-height:16.6px;width:470px;margin:12px auto 0}
.touch .pill{width:93px;height:28px;margin-top:15px}
.touch-mark{left:35px;top:1638px;width:80px;height:80px;border-radius:50%;background:var(--taupe)}

/* news */
.news-card{position:absolute;top:1778px;width:181px;height:182px;background:var(--white);border:1px solid #d9d9d9;border-radius:6px;padding:8px}
.news-img{width:164px;height:90px}
.news-img--a{background:linear-gradient(180deg,#c98a74 0%,#6d6c5a 55%,#5d7d3d 100%)}
.news-img--b{background:linear-gradient(180deg,#e3cdb4 0%,#c59b72 55%,#7b5a3e 100%)}
.news-img--c{background:linear-gradient(180deg,#e7e8ea 0%,#bdbfc2 55%,#6f6a63 100%)}
.news-tag{font-family:"Inter",sans-serif;font-size:6px;color:var(--muted);margin-top:12px}
.news-title{font-family:"Inter",sans-serif;font-weight:600;font-size:7.3px;line-height:13px;color:var(--ink);margin-top:4px}
.news-date{font-family:"Inter",sans-serif;font-size:6.5px;color:#b7bf2a;margin-top:6px}
.news-arrow{position:absolute;right:14px;bottom:12px}

/* footer */
.footer{left:0;top:1940px;width:724px;height:266px;background:var(--footer)}
.footer-brand{left:66px;top:2002px;display:flex;align-items:center;gap:7px}
.footer-brand .brand-dot{width:32px;height:32px;background:var(--taupe)}
.footer-brand .brand-name{color:var(--taupe);font-weight:500;font-size:12.5px}
.socials{left:78px;top:2050px;display:flex;gap:13px}
.socials span{width:14px;height:14px;border-radius:50%;background:#8a7f79}
.col{top:2002px}
.col h6{font-family:"Inter",sans-serif;font-weight:500;font-size:11.5px;color:var(--ink);margin-bottom:9px}
.col li{list-style:none;font-size:8.3px;line-height:20.8px;color:#333}
.contact-row{display:flex;gap:9px;font-size:8.3px;line-height:16.6px;color:#333;margin-bottom:9px;align-items:flex-start}
.contact-row i{flex:none;width:17px;height:17px;border-radius:50%;background:var(--taupe);display:flex;align-items:center;justify-content:center}
.rule{left:66px;top:2150px;width:590px;height:1px;background:#cfcfcf}
.copy{left:0;top:2172px;width:724px;text-align:center;font-size:8.5px;color:var(--ink)}
</style>
</head>
<body>
<main class="board">

<!-- Variant A -->
<section class="page page--a">
  <header class="hero hero--family">
    <div class="hero-photo" role="img" aria-label="Family running through a sunlit meadow"></div>
    <div class="brand"><span class="brand-dot"></span><span class="brand-name">Laanemetsa<br>Haldusgrupp</span></div>
    <div class="lang">En
      <svg width="12" height="12" viewBox="0 0 12 12" fill="none" stroke="#fff" stroke-width="1"><circle cx="6" cy="6" r="5"/><path d="M1 6h10M6 1c2 2 2 8 0 10M6 1c-2 2-2 8 0 10"/></svg>
      <svg width="7" height="5" viewBox="0 0 7 5" fill="none" stroke="#fff"><path d="M1 1l2.5 2.5L6 1"/></svg></div>
    <a class="pill pill--lime header-cta">Contact Us</a>
    <svg class="menu" width="18" height="14" viewBox="0 0 18 14" stroke="#fff" stroke-width="1.6"><path d="M4 1h14M0 7h18M6 13h12"/></svg>
    <div class="hero-copy">
      <div class="eyebrow">Welcome to</div>
      <h1>Laanemetsa Haldusgrupp</h1>
      <p>Laanemetsa Haldusgrupp is Estonia's leading group providing waste management and municipal services, whose main activity is household waste collection.</p>
      <a class="pill pill--white">Get Started</a>
    </div>
  </header>

  <h2 class="section-title" style="top:410px">About Laanemetsa Haldusgrupp</h2>
  <div class="abs about-art" role="img" aria-label="Large brand decoration in taupe and lime"></div>
  <div class="abs about-text">
    <p>Laanemetsa Haldusgrupp is Estonia's leading group providing waste management and municipal services, whose main activity is household wastecollection. In addition, the company deals with secondary raw materials, construction waste and other waste collection. In some regions, the company also offers maintenance services for roads and streets during the winter.</p>
    <p>The company serves More than 100,000 customers in Estonia and handles over 250,000 tons of waste per year. The group employs nearly 600 people and its turnover exceeded 2016. 28 million euros in The integrated occupational health, occupational safety, quality and environmental management system ISO has been implemented in the companyBased on 9001, ISO 14001 and ISO 45001 standards.</p>
    <a class="pill pill--lime read-more" style="margin-top:14px">Read More</a>
  </div>

  <div class="abs benefits">
    <h2 class="section-title" style="top:32px">Our Benefits</h2>
    <p class="lead" style="top:66px">Temporibus autem quibusdam et aut officiis debitis aut rerum necessitatibus saepe eveniet ut et voluptates repudiandae sint et molestiae non recusandae.</p>
    <div class="card" style="left:67px"><span class="card-icon"></span><h4>We manage waste collection</h4><p>Itaque earum rerum hic tenetur a sapiente delectus, ut aut reiciendis voluptatibus maiores alias conseq uatur aut perferendis.</p></div>
    <div class="card" style="left:270px"><span class="card-icon"></span><h4>Recycling for 100K+ households</h4><p>Itaque earum rerum hic tenetur a sapiente delectus, ut aut reiciendis voluptatibus maiores alias conseq uatur aut perferendis.</p></div>
    <div class="card" style="left:472px"><span class="card-icon"></span><h4>Businesses across Estonia</h4><p>Itaque earum rerum hic tenetur a sapiente delectus, ut aut reiciendis voluptatibus maiores alias conseq uatur aut perferendis.</p></div>
  </div>

  <h2 class="section-title" style="top:1089px">Itaque earum rerum hic tenetur</h2>
  <div class="abs steps">
    <h3>Temporibus autem quibusdam</h3>
    <div class="step"><span class="step-num">1</span><h5>Nam libero tempore, cum soluta nobis</h5><p>Nam libero tempore, cum soluta nobis est eligendi optio cumque nihil impedit quo minus id quod maxime placeat facere possimus, omnis voluptas assumenda est, omnis dolor repellendus.</p></div>
    <div class="step"><span class="step-num">2</span><h5>Dignissimos ducimus qui blanditiis</h5><p>Nam libero tempore, cum soluta nobis est eligendi optio cumque nihil impedit quo minus id quod.</p></div>
    <div class="step"><span class="step-num">3</span><h5>Ducimus qui blanditiis</h5><p>Itaque earum rerum hic tenetur a sapiente delectus, ut aut reiciendis voluptatibus maiores alias consequatur aut perferendis doloribus asperiores repellat.</p></div>
    <a class="pill pill--lime read-more">Read More</a>
  </div>
  <div class="abs forest" role="img" aria-label="Aerial view of forest with lakes shaped like a recycling sign"></div>

  <div class="abs touch-mark"></div>
  <div class="abs touch">
    <h2 class="section-title">Get In Touch with Us</h2>
    <p>Temporibus autem quibusdam et aut officiis debitis aut rerum necessitatibus minus id quod maxime placeat facere possimus, omnis voluptas assumenda est, omnis dolorsaepe eveniet ut et voluptates repudiandae sint et molestiae non recusandae.</p>
    <p style="margin-top:16px">Itaque earum rerum hic tenetur a sapiente delectus, ut aut reiciendis voluptatibus maiores alias consequatur aut perferendis doloribus asperiores repellat</p>
    <a class="pill pill--white">Contact Us</a>
  </div>

  <div class="abs footer"></div>
  <h2 class="section-title" style="top:1728px">Latest News</h2>
  <article class="news-card" style="left:67px"><div class="news-img news-img--a" role="img" aria-label="Wildflower meadow at sunset"></div><div class="news-tag">ARTICLE</div><div class="news-title">Temporibus autem quibusdam et aut officiis essitatibus saepe</div><div class="news-date">11 June 2024</div><svg class="news-arrow" width="14" height="14" viewBox="0 0 14 14" fill="none" stroke="#666"><rect x=".5" y=".5" width="13" height="13" rx="3"/><path d="M4 7h6M8 5l2 2-2 2"/></svg></article>
  <article class="news-card" style="left:270px"><div class="news-img news-img--b" role="img" aria-label="Friends celebrating on a hilltop"></div><div class="news-tag">ARTICLE</div><div class="news-title">Temporibus autem quibusdam et aut officiis essitatibus saepe</div><div class="news-date">12 June 2024</div><svg class="news-arrow" width="14" height="14" viewBox="0 0 14 14" fill="none" stroke="#666"><rect x=".5" y=".5" width="13" height="13" rx="3"/><path d="M4 7h6M8 5l2 2-2 2"/></svg></article>
  <article class="news-card" style="left:474px"><div class="news-img news-img--c" role="img" aria-label="Team working together at an office table"></div><div class="news-tag">ARTICLE</div><div class="news-title">Temporibus autem quibusdam et aut officiis essitatibus saepe</div><div class="news-date">09 June 2024</div><svg class="news-arrow" width="14" height="14" viewBox="0 0 14 14" fill="none" stroke="#666"><rect x=".5" y=".5" width="13" height="13" rx="3"/><path d="M4 7h6M8 5l2 2-2 2"/></svg></article>

  <div class="abs footer-brand"><span class="brand-dot"></span><span class="brand-name">Laanemetsa<br>Haldusgrupp</span></div>
  <div class="abs socials"><span></span><span></span><span></span><span></span></div>
  <div class="abs col" style="left:253px"><h6>Quick Links</h6><ul><li>Home</li><li>About</li><li>Environmental services</li><li>Recycling</li><li>Contact Us</li></ul></div>
  <div class="abs col" style="left:375px"><h6>Help Links</h6><ul><li>FAQ</li><li>Terms of use</li><li>Privacy Policy</li><li>Support Links</li><li>Conditions</li></ul></div>
  <div class="abs col" style="left:484px"><h6>Contact Us</h6>
    <div class="contact-row"><i><svg width="8" height="10" viewBox="0 0 8 10" fill="#fff"><path d="M4 0a4 4 0 0 1 4 4c0 3-4 6-4 6S0 7 0 4a4 4 0 0 1 4-4z"/></svg></i><span>Laanemetsa Haldusgrupp<br>United States</span></div>
    <div class="contact-row"><i><svg width="9" height="9" viewBox="0 0 9 9" fill="#fff"><path d="M1 0h2l1 2-1 1a5 5 0 0 0 3 3l1-1 2 1v2c-4 0-8-4-8-8z"/></svg></i><span>+372 555 0142</span></div>
    <div class="contact-row"><i><svg width="9" height="7" viewBox="0 0 9 7" fill="none" stroke="#fff"><rect x=".5" y=".5" width="8" height="6"/><path d="M.5.5l4 3 4-3"/></svg></i><span>info@laanemetsahaldus.ee</span></div>
  </div>
  <div class="abs rule"></div>
  <p class="abs copy">Copyrights@2024.Laanemetsa Haldusgrupp.All Rights Reserved</p>
</section>

<!-- Variant B -->
<section class="page page--b">
  <header class="hero hero--globe">
    <div class="hero-globe" role="img" aria-label="Glass globe in grass surrounded by sustainability icons"></div>
    <div class="brand"><span class="brand-dot"></span><span class="brand-name">Laanemetsa<br>Haldusgrupp</span></div>
    <div class="lang">En
      <svg width="12" height="12" viewBox="0 0 12 12" fill="none" stroke="#fff" stroke-width="1"><circle cx="6" cy="6" r="5"/><path d="M1 6h10M6 1c2 2 2 8 0 10M6 1c-2 2-2 8 0 10"/></svg>
      <svg width="7" height="5" viewBox="0 0 7 5" fill="none" stroke="#fff"><path d="M1 1l2.5 2.5L6 1"/></svg></div>
    <a class="pill pill--lime header-cta">Contact Us</a>
    <svg class="menu" width="18" height="14" viewBox="0 0 18 14" stroke="#fff" stroke-width="1.6"><path d="M4 1h14M0 7h18M6 13h12"/></svg>
    <div class="hero-copy">
      <div class="eyebrow">Welcome to</div>
      <h1>Laanemetsa Haldusgrupp</h1>
      <p>Laanemetsa Haldusgrupp is Estonia's leading group providing waste management and municipal services, whose main activity is household waste collection.</p>
      <a class="pill pill--white">Get Started</a>
    </div>
  </header>

  <h2 class="section-title" style="top:410px">About Laanemetsa Haldusgrupp</h2>
  <div class="abs about-art" role="img" aria-label="Large brand decoration in taupe and lime"></div>
  <div class="abs about-text">
    <p>Laanemetsa Haldusgrupp is Estonia's leading group providing waste management and municipal services, whose main activity is household wastecollection. In addition, the company deals with secondary raw materials, construction waste and other waste collection. In some regions, the company also offers maintenance services for roads and streets during the winter.</p>
    <p>The company serves More than 100,000 customers in Estonia and handles over 250,000 tons of waste per year. The group employs nearly 600 people and its turnover exceeded 2016. 28 million euros in The integrated occupational health, occupational safety, quality and environmental management system ISO has been implemented in the companyBased on 9001, ISO 14001 and ISO 45001 standards.</p>
    <a class="pill pill--lime read-more" style="margin-top:14px">Read More</a>
  </div>

  <div class="abs benefits">
    <h2 class="section-title" style="top:32px">Our Benefits</h2>
    <p class="lead" style="top:66px">Temporibus autem quibusdam et aut officiis debitis aut rerum necessitatibus saepe eveniet ut et voluptates repudiandae sint et molestiae non recusandae.</p>
    <div class="card" style="left:67px"><span class="card-icon"></span><h4>We manage waste collection</h4><p>Itaque earum rerum hic tenetur a sapiente delectus, ut aut reiciendis voluptatibus maiores alias conseq uatur aut perferendis.</p></div>
    <div class="card" style="left:270px"><span class="card-icon"></span><h4>Recycling for 100K+ households</h4><p>Itaque earum rerum hic tenetur a sapiente delectus, ut aut reiciendis voluptatibus maiores alias conseq uatur aut perferendis.</p></div>
    <div class="card" style="left:472px"><span class="card-icon"></span><h4>Businesses across Estonia</h4><p>Itaque earum rerum hic tenetur a sapiente delectus, ut aut reiciendis voluptatibus maiores alias conseq uatur aut perferendis.</p></div>
  </div>

  <h2 class="section-title" style="top:1089px">Itaque earum rerum hic tenetur</h2>
  <div class="abs steps">
    <h3>Temporibus autem quibusdam</h3>
    <div class="step"><span class="step-num">1</span><h5>Nam libero tempore, cum soluta nobis</h5><p>Nam libero tempore, cum soluta nobis est eligendi optio cumque nihil impedit quo minus id quod maxime placeat facere possimus, omnis voluptas assumenda est, omnis dolor repellendus.</p></div>
    <div class="step"><span class="step-num">2</span><h5>Dignissimos ducimus qui blanditiis</h5><p>Nam libero tempore, cum soluta nobis est eligendi optio cumque nihil impedit quo minus id quod.</p></div>
    <div class="step"><span class="step-num">3</span><h5>Ducimus qui blanditiis</h5><p>Itaque earum rerum hic tenetur a sapiente delectus, ut aut reiciendis voluptatibus maiores alias consequatur aut perferendis doloribus asperiores repellat.</p></div>
    <a class="pill pill--lime read-more">Read More</a>
  </div>
  <div class="abs forest" role="img" aria-label="Aerial view of forest with lakes shaped like a recycling sign"></div>

  <div class="abs touch-mark"></div>
  <div class="abs touch">
    <h2 class="section-title">Get In Touch with Us</h2>
    <p>Temporibus autem quibusdam et aut officiis debitis aut rerum necessitatibus minus id quod maxime placeat facere possimus, omnis voluptas assumenda est, omnis dolorsaepe eveniet ut et voluptates repudiandae sint et molestiae non recusandae.</p>
    <p style="margin-top:16px">Itaque earum rerum hic tenetur a sapiente delectus, ut aut reiciendis voluptatibus maiores alias consequatur aut perferendis doloribus asperiores repellat</p>
    <a class="pill pill--white">Contact Us</a>
  </div>

  <div class="abs footer"></div>
  <h2 class="section-title" style="top:1728px">Latest News</h2>
  <article class="news-card" style="left:67px"><div class="news-img news-img--a" role="img" aria-label="Wildflower meadow at sunset"></div><div class="news-tag">ARTICLE</div><div class="news-title">Temporibus autem quibusdam et aut officiis essitatibus saepe</div><div class="news-date">11 June 2024</div><svg class="news-arrow" width="14" height="14" viewBox="0 0 14 14" fill="none" stroke="#666"><rect x=".5" y=".5" width="13" height="13" rx="3"/><path d="M4 7h6M8 5l2 2-2 2"/></svg></article>
  <article class="news-card" style="left:270px"><div class="news-img news-img--b" role="img" aria-label="Friends celebrating on a hilltop"></div><div class="news-tag">ARTICLE</div><div class="news-title">Temporibus autem quibusdam et aut officiis essitatibus saepe</div><div class="news-date">12 June 2024</div><svg class="news-arrow" width="14" height="14" viewBox="0 0 14 14" fill="none" stroke="#666"><rect x=".5" y=".5" width="13" height="13" rx="3"/><path d="M4 7h6M8 5l2 2-2 2"/></svg></article>
  <article class="news-card" style="left:474px"><div class="news-img news-img--c" role="img" aria-label="Team working together at an office table"></div><div class="news-tag">ARTICLE</div><div class="news-title">Temporibus autem quibusdam et aut officiis essitatibus saepe</div><div class="news-date">09 June 2024</div><svg class="news-arrow" width="14" height="14" viewBox="0 0 14 14" fill="none" stroke="#666"><rect x=".5" y=".5" width="13" height="13" rx="3"/><path d="M4 7h6M8 5l2 2-2 2"/></svg></article>

  <div class="abs footer-brand"><span class="brand-dot"></span><span class="brand-name">Laanemetsa<br>Haldusgrupp</span></div>
  <div class="abs socials"><span></span><span></span><span></span><span></span></div>
  <div class="abs col" style="left:253px"><h6>Quick Links</h6><ul><li>Home</li><li>About</li><li>Environmental services</li><li>Recycling</li><li>Contact Us</li></ul></div>
  <div class="abs col" style="left:375px"><h6>Help Links</h6><ul><li>FAQ</li><li>Terms of use</li><li>Privacy Policy</li><li>Support Links</li><li>Conditions</li></ul></div>
  <div class="abs col" style="left:484px"><h6>Contact Us</h6>
    <div class="contact-row"><i><svg width="8" height="10" viewBox="0 0 8 10" fill="#fff"><path d="M4 0a4 4 0 0 1 4 4c0 3-4 6-4 6S0 7 0 4a4 4 0 0 1 4-4z"/></svg></i><span>Laanemetsa Haldusgrupp<br>United States</span></div>
    <div class="contact-row"><i><svg width="9" height="9" viewBox="0 0 9 9" fill="#fff"><path d="M1 0h2l1 2-1 1a5 5 0 0 0 3 3l1-1 2 1v2c-4 0-8-4-8-8z"/></svg></i><span>+372 555 0142</span></div>
    <div class="contact-row"><i><svg width="9" height="7" viewBox="0 0 9 7" fill="none" stroke="#fff"><rect x=".5" y=".5" width="8" height="6"/><path d="M.5.5l4 3 4-3"/></svg></i><span>info@laanemetsahaldus.ee</span></div>
  </div>
  <div class="abs rule"></div>
  <p class="abs copy">Copyrights@2024.Laanemetsa Haldusgrupp.All Rights Reserved</p>
</section>

</main>
</body>
</html>
```